Product Label for Health Supplement

Design a product label to go on the jar. The product is a health supplement super-food called Moringa oleifera (Moringa leaf).

This product will be sold online at velarotin.com.au and in health-food stores. For inspiration, you can see Velarotin's 2 products on velarotin.com.au which are in a jar size similar to this new product.

The label needs to be attractive and feels natural and healthy.

A content template has been prepared for you. Please use all the content from the template in your design concept. There is no need to add new text. Please keep the text provided in the template.

The label has been setout in left, front, and right sides.
Here is the link to the template (also attached to the design brief) https://www.plinkspace.example/file/93KdTwqBz81LmNpXrYeUa4/Untitled?type=design&node-id=0%3A1&t=QHpRtcWmzE5aLbGo-1

Required Label Design Specifications:
Max Length: 275mm
Max Height: 70mm
DPI: 300 (at least)
Colour: CMYK
Minimum font: 5pt
Bleed: 1.5mm
Safe zone: 3mm from edge all around.

Once approved, the design will need to be delivered in CMYK color and in PDF format.

The Art Guidelines have been attached.

```html
<!DOCTYPE html>
<html lang="en">
<head>
<meta charset="utf-8">
<title>Velarotin Organic Moringa Label</title>
<link rel="stylesheet" href="https://fonts.googleapis.com/css2?family=Montserrat:wght@600;800;900&family=Fira+Sans+Condensed:ital,wght@1,500&family=Fira+Sans:ital,wght@1,600&family=Open+Sans:wght@400;700&display=swap">
<style>
  :root {
    --canvas-bg: #e9ece7;
    --label-white: #ffffff;
    --forest: #0f6a3b;
    --lime: #8cc63f;
    --leaf-green: #7cb342;
    --ink: #1a1a1a;
    --pale-leaf: #dfe8e3;
  }
  html, body {
    margin: 0;
    padding: 0;
    width: 1200px;
    height: 1200px;
    overflow: hidden;
    background: var(--canvas-bg);
  }
  .label {
    position: absolute;
    left: 60px;
    top: 170px;
    width: 1080px;
    height: 860px;
    background: var(--label-white);
    overflow: hidden;
    box-shadow: 0 6px 24px rgba(0,0,0,0.12);
  }
  .label-shapes {
    position: absolute;
    inset: 0;
  }
  .quality-seal {
    position: absolute;
    left: 48px;
    top: 62px;
    width: 112px;
    height: 112px;
    border-radius: 50%;
    background: var(--forest);
    border: 6px solid var(--leaf-green);
    box-sizing: border-box;
  }
  .brand-name {
    position: absolute;
    left: 0;
    width: 1080px;
    top: 92px;
    text-align: center;
    font-family: "Montserrat", sans-serif;
    font-weight: 600;
    font-size: 72px;
    letter-spacing: 1px;
    color: var(--ink);
    line-height: 1;
  }
  .lab-tested {
    position: absolute;
    left: 900px;
    top: 40px;
    width: 130px;
    text-align: center;
    font-family: "Open Sans", sans-serif;
    font-weight: 700;
    font-size: 19px;
    color: var(--ink);
  }
  .lab-tested svg { display: block; margin: 0 auto 4px; }
  .product-type {
    position: absolute;
    left: 215px;
    top: 222px;
    font-family: "Montserrat", sans-serif;
    font-weight: 800;
    font-size: 56px;
    color: var(--leaf-green);
    line-height: 1;
  }
  .product-name {
    position: absolute;
    left: 210px;
    top: 272px;
    font-family: "Montserrat", sans-serif;
    font-weight: 900;
    font-size: 122px;
    letter-spacing: -2px;
    color: var(--ink);
    line-height: 1;
  }
  .product-desc {
    position: absolute;
    left: 212px;
    top: 398px;
    font-family: "Fira Sans", sans-serif;
    font-style: italic;
    font-weight: 600;
    font-size: 44px;
    color: var(--ink);
    line-height: 1;
  }
  .leaf-art {
    position: absolute;
    left: 14px;
    top: 500px;
    width: 286px;
    height: 320px;
    border-radius: 40% 50% 45% 50%;
    background: radial-gradient(circle at 45% 45%, #8fc54a 0%, #6aa83a 55%, rgba(15,106,59,0) 75%);
  }
  .benefits {
    position: absolute;
    left: 345px;
    top: 580px;
    margin: 0;
    padding: 0;
    list-style: none;
    font-family: "Fira Sans Condensed", sans-serif;
    font-style: italic;
    font-weight: 500;
    font-size: 46px;
    color: #ffffff;
  }
  .benefits li {
    display: flex;
    align-items: center;
    height: 75px;
  }
  .benefits li::before {
    content: "";
    width: 22px;
    height: 22px;
    margin-right: 12px;
    border: 3px solid #ffffff;
    border-radius: 0 50% 50% 50%;
    transform: rotate(45deg);
    box-sizing: border-box;
  }
  .pack-info {
    position: absolute;
    color: #ffffff;
    text-align: center;
    font-family: "Open Sans", sans-serif;
    line-height: 1.1;
  }
  .pack-info strong {
    display: block;
    font-weight: 700;
  }
  .serves { left: 880px; top: 505px; width: 150px; font-size: 30px; }
  .serves strong { font-size: 38px; }
  .net-weight { left: 860px; top: 725px; width: 200px; font-size: 32px; transform: rotate(-4deg); }
  .net-weight strong { font-size: 44px; }
</style>
</head>
<body>
  <div class="label">
    <svg class="label-shapes" width="1080" height="860" viewBox="0 0 1080 860" aria-hidden="true">
      <path d="M0,430 Q520,640 1080,430 L1080,860 L0,860 Z" fill="var(--forest)"/>
      <path d="M0,420 Q480,600 1000,470" fill="none" stroke="var(--lime)" stroke-width="12" stroke-linecap="round"/>
    </svg>

    <div class="quality-seal" aria-hidden="true"></div>
    <div class="brand-name">velarotin</div>
    <div class="lab-tested">
      <svg width="44" height="54" viewBox="0 0 44 54" aria-hidden="true">
        <path d="M16,4 L28,4 L28,20 L42,50 L2,50 L16,20 Z" fill="var(--forest)"/>
        <path d="M8,38 L36,38 L42,50 L2,50 Z" fill="var(--lime)"/>
      </svg>
      Lab Tested
    </div>

    <div class="product-type">ORGANIC</div>
    <div class="product-name">MORINGA</div>
    <div class="product-desc">Premium-Grade Leaf Powder</div>

    <div class="leaf-art" role="img" aria-label="Illustration of a sprig of moringa leaves"></div>

    <ul class="benefits">
      <li>Naturally Air-Dried</li>
      <li>No Irradiation/Chemicals</li>
      <li>No Cheap ‘Fillers’</li>
    </ul>

    <div class="pack-info serves"><strong>30</strong>Serves</div>
    <div class="pack-info net-weight"><strong>150G</strong>Net Weight</div>
  </div>
</body>
</html>
```